Tech business card design

We need an amazing business card design for our new business 'Pexla' a marketing tech startup based in Sydney, Australia. We provide an online marketplace for businesses to search and buy advertising media, connect with service providers and learn more about marketing. We wish to communicate 'cool tech', reliability and professionalism and design based around our logo.

Target Market(s)

Business Owners

Contact Information for Business Card

Name
Position
Email Address
Website
Phone Number

Font styles to use
Other font styles liked:
• Avenir & Avenir Next

Colors

Designer to choose colors to be used in the design.

```html
<!DOCTYPE html>
<html lang="en">
<head>
<meta charset="utf-8">
<title>Pexla Business Card</title>
<link rel="stylesheet" href="https://fonts.googleapis.com/css2?family=Exo+2:wght@400;700;800&family=Oswald:wght@600&display=swap">
<style>
  :root {
    --stage: #d9d9db;
    --navy: #0e0d3b;
    --paper: #fcf8f7;
    --ink: #1b1a47;
    --text: #2b2b33;
    --muted: #55555f;
    --rule: #c9c6c6;
    --white: #ffffff;
  }
  * { box-sizing: border-box; margin: 0; padding: 0; }
  html, body {
    width: 1200px; height: 782px; overflow: hidden;
    background: var(--stage);
  }
  .canvas {
    position: relative; width: 1200px; height: 782px;
  }
  .card {
    position: absolute; top: 236px;
    width: 540px; height: 310px;
    box-shadow: 0 6px 18px rgba(0,0,0,0.18);
  }
  .card--back { left: 40px; background: var(--paper); }
  .card--front { left: 620px; background: var(--navy); display: flex; align-items: center; justify-content: center; }

  .brand-name {
    font-family: "Exo 2", sans-serif;
    font-weight: 800;
    font-size: 96px;
    letter-spacing: -2px;
    color: var(--white);
    line-height: 1;
  }

  .identity {
    position: absolute; right: 270px; top: 128px;
    text-align: right;
  }
  .person-name {
    font-family: "Oswald", sans-serif;
    font-weight: 600;
    font-size: 22px;
    letter-spacing: 0.3px;
    color: var(--ink);
    text-transform: uppercase;
    line-height: 1.1;
  }
  .person-role {
    font-family: "Exo 2", sans-serif;
    font-size: 13px;
    letter-spacing: 0.6px;
    color: var(--muted);
  }
  .divider {
    position: absolute; left: 287px; top: 116px;
    width: 1px; height: 78px; background: var(--rule);
  }
  .contacts {
    position: absolute; left: 306px; top: 116px;
    list-style: none;
  }
  .contact-item {
    display: flex; align-items: center; gap: 8px;
    font-family: "Exo 2", sans-serif;
    font-size: 15px;
    letter-spacing: 0.6px;
    color: var(--text);
    height: 26px;
  }
  .contact-icon { width: 12px; height: 12px; fill: var(--ink); flex: none; }
</style>
</head>
<body>
<main class="canvas">
  <section class="card card--back" aria-label="Card back with contact details">
    <div class="identity">
      <p class="person-name">Marcus Hale</p>
      <p class="person-role">Managing Director</p>
    </div>
    <div class="divider"></div>
    <ul class="contacts">
      <li class="contact-item">
        <svg class="contact-icon" viewBox="0 0 12 12" aria-hidden="true"><path d="M1 3.5C1 2 2.5 1 6 1s5 1 5 2.5v1H8.5V3.5h-5v1H1z"/><rect x="2" y="5.5" width="8" height="5.5" rx="1"/></svg>
        <span>044-987 650 321</span>
      </li>
      <li class="contact-item">
        <svg class="contact-icon" viewBox="0 0 12 12" aria-hidden="true"><rect x="0.5" y="2" width="11" height="8" rx="1"/><path d="M1 2.6l5 3.6 5-3.6" stroke="#fcf8f7" stroke-width="1" fill="none"/></svg>
        <span>hello@pexlamail.com</span>
      </li>
      <li class="contact-item">
        <svg class="contact-icon" viewBox="0 0 12 12" aria-hidden="true"><circle cx="6" cy="6" r="5.5"/><path d="M0.5 6h11M6 0.5c-2.5 3-2.5 8 0 11M6 0.5c2.5 3 2.5 8 0 11" stroke="#fcf8f7" stroke-width="0.8" fill="none"/></svg>
        <span>www.pexlamedia.com</span>
      </li>
    </ul>
  </section>

  <section class="card card--front" aria-label="Card front with company name">
    <p class="brand-name">Pexla</p>
  </section>
</main>
</body>
</html>
```